Ward Compass Business Card Design*

We need a business card design for our company Ward Compass. Our company is specialized in providing online consulting services regarding medical institutions, hospitals and doctors. We work with patients worldwide looking to choose between healthcare providers. We have a website you may use as a reference, where we list doctors and clinics worldwide. So we target Medical providers as well as patients worldwide.
Target Market(s)
Medical Providers and patients around the world
Industry/Entity Type
Medical
Contact Information for Business Card
Salwa Kettani
CEO
+90 612 348 2175
info@wardcompass.example
www.wardcompass.example
14 Annakhil 7 H.R.B. Rabat, Morocco
Requirements
Must have
- Company logo/name on one full side, personal info and smaller logo and company name on the other side.
Nice to have
- Smart and elegant design

```html
<!DOCTYPE html>
<html lang="en">
<head>
<meta charset="utf-8">
<title>Ward Compass Business Card</title>
<link rel="stylesheet" href="https://fonts.googleapis.com/css2?family=Nunito+Sans:wght@400;700;800&display=swap">
<style>
  :root {
    --navy: #1a4475;
    --paper: #f2f2f4;
    --rule: #8a8f98;
    --grey: #858585;
    --ink: #3a3a3a;
    --white: #ffffff;
    --backdrop: #e4e1dc;
  }
  * { margin: 0; padding: 0; box-sizing: border-box; }
  html, body {
    width: 900px; height: 1200px; overflow: hidden;
    background: var(--backdrop);
    font-family: "Nunito Sans", Arial, sans-serif;
  }
  .stage { position: relative; width: 900px; height: 1200px; }
  .card {
    position: absolute; left: 77px; width: 746px; height: 437px;
    box-shadow: 0 3px 8px rgba(0,0,0,0.25);
    overflow: hidden;
  }
  .card--front { top: 134px; background: var(--paper); }
  .card--back { top: 638px; background: var(--navy); }

  .front-band {
    position: absolute; left: 0; top: 0; width: 100%; height: 227px;
    background: var(--navy);
  }
  .front-rule {
    position: absolute; left: 0; top: 232px; width: 100%; height: 1px;
    background: var(--rule);
  }
  .brand {
    position: absolute; display: flex; align-items: center;
    color: var(--white); font-weight: 800; letter-spacing: 0.01em;
    white-space: nowrap;
  }
  .brand-mark { border-radius: 50%; background: var(--white); flex: none; }
  .brand--small { right: 52px; top: 64px; font-size: 26px; }
  .brand--small .brand-mark { width: 22px; height: 22px; margin-right: 12px; }
  .brand--large { left: 50%; top: 211px; transform: translate(-50%, -50%); font-size: 46px; }
  .brand--large .brand-mark { width: 38px; height: 38px; margin-right: 22px; }

  .holder {
    position: absolute; left: 44px; top: 186px; color: var(--white);
    font-size: 27px; letter-spacing: 0.01em; white-space: nowrap;
  }
  .holder-first { font-weight: 800; }
  .holder-last { font-weight: 400; }
  .holder-role { font-size: 12px; margin-left: 18px; vertical-align: 1px; }

  .contacts {
    position: absolute; left: 55px; top: 356px; color: var(--ink);
    font-size: 17.5px; line-height: 24px;
  }
  .contact-row { display: flex; align-items: center; }
  .contact-icon { width: 16px; height: 16px; margin-right: 12px; fill: var(--ink); }
  .address {
    position: absolute; left: 516px; top: 356px; color: var(--ink);
    font-size: 17.5px; line-height: 24px; font-style: normal;
  }
  .website {
    position: absolute; left: 0; width: 100%; top: 399px; text-align: center;
    color: var(--white); font-size: 16px; letter-spacing: 0.22em;
  }
</style>
</head>
<body>
<main class="stage">
  <section class="card card--front">
    <div class="front-band"></div>
    <div class="front-rule"></div>
    <div class="brand brand--small"><span class="brand-mark"></span>WARD COMPASS</div>
    <p class="holder"><span class="holder-first">SALWA</span> <span class="holder-last">KETTANI</span><span class="holder-role">CEO</span></p>
    <div class="contacts">
      <div class="contact-row">
        <svg class="contact-icon" viewBox="0 0 16 16" aria-hidden="true"><path d="M3.5 1.2l2.4 2.6-1.2 2c.9 2 2.6 3.7 4.6 4.6l2-1.2 2.6 2.4-1.3 2.4C7 13.6 2.4 9 1.2 4.5z"/></svg>
        <span>+90 612 348 2175</span>
      </div>
      <div class="contact-row">
        <svg class="contact-icon" viewBox="0 0 16 16" aria-hidden="true"><path d="M1 3.5h14v9H1z M1.8 4.2L8 9l6.2-4.8" stroke="#f2f2f4" stroke-width="1.1"/></svg>
        <span>info@wardcompass.example</span>
      </div>
    </div>
    <address class="address">14 Annakhil 7 H.R.B.<br>Rabat, Morocco</address>
  </section>

  <section class="card card--back">
    <div class="brand brand--large"><span class="brand-mark"></span>WARD COMPASS</div>
    <p class="website">www.wardcompass.example</p>
  </section>
</main>
</body>
</html>
```